Realtor branding business card

modern, simple and self branding. Broker office logo needs to be used but not emphasized. Looking to brand myself

Target Market(s)

buyers, sellers and investors

Industry/Entity Type

Realtor

Contact Information for Business Card

Sample of my current business card on file

Requirements
Must have
• my website - tobiasmerrowkl.com
• Realtor logo
• Fair housing logo
Nice to have
• Colors from office logo but not a must
Should not have
• Do not want headshot

```html
<!DOCTYPE html>
<html lang="en">
<head>
<meta charset="utf-8">
<title>Tobias Merrow – Business Card</title>
<link href="https://fonts.googleapis.com/css2?family=Lato:wght@400;700;900&display=swap" rel="stylesheet">
<style>
  :root {
    --navy: #24166a;
    --red: #d9241c;
    --paper: #ffffff;
    --ink: #333333;
    --muted: #8a86a8;
    --backdrop: #f2f2f2;
  }
  * { margin: 0; padding: 0; box-sizing: border-box; }
  html, body {
    width: 1200px;
    height: 757px;
    overflow: hidden;
    background: var(--backdrop);
    font-family: 'Lato', sans-serif;
  }
  .canvas { position: relative; width: 1200px; height: 757px; }
  .card {
    position: absolute;
    top: 195px;
    width: 499px;
    height: 299px;
    overflow: hidden;
  }
  .card-front { left: 85px; background: var(--paper); }
  .card-back  { left: 650px; background: var(--navy); }

  .brand-name { position: absolute; font-weight: 900; line-height: 1; }
  .card-front .brand-name { left: 50px; top: 116px; color: var(--navy); }
  .card-back .brand-name  { left: 32px; top: 216px; color: var(--paper); }
  .brand-line-main { display: block; font-size: 28px; letter-spacing: -0.3px; }
  .brand-line-sub  { display: block; font-size: 14px; font-weight: 700; margin-top: 3px; letter-spacing: 0.3px; }

  .badges {
    position: absolute;
    left: 50px;
    top: 176px;
    display: flex;
    gap: 10px;
  }
  .badge { width: 22px; height: 22px; background: var(--navy); }
  .badge-round { border-radius: 50%; }

  .divider {
    position: absolute;
    left: 262px;
    top: 73px;
    width: 2px;
    height: 145px;
    background: linear-gradient(to bottom, rgba(36,22,106,0), var(--navy) 50%, rgba(36,22,106,0));
  }

  .contact { position: absolute; left: 296px; top: 76px; color: var(--navy); }
  .agent-name { font-size: 16px; font-weight: 900; color: var(--red); }
  .agent-title { font-size: 10.5px; color: var(--ink); margin-top: 3px; }
  .address { font-size: 9.5px; font-weight: 700; line-height: 15px; margin-top: 18px; }
  .contact-list { list-style: none; margin-top: 16px; }
  .contact-list li {
    display: flex;
    align-items: center;
    font-size: 9.5px;
    color: var(--ink);
    height: 17px;
  }
  .contact-list svg { width: 10px; height: 10px; margin-right: 9px; flex: none; }

  .back-website {
    position: absolute;
    right: 30px;
    bottom: 30px;
    font-size: 12px;
    font-weight: 700;
    color: var(--paper);
    letter-spacing: 0.5px;
  }

  .footer-band { position: absolute; left: 0; bottom: 0; width: 499px; height: 25px; }
</style>
</head>
<body>
<main class="canvas">
  <section class="card card-front" aria-label="Business card front">
    <div class="brand-name">
      <span class="brand-line-main">Brightgate</span>
      <span class="brand-line-sub">Realty Group</span>
    </div>
    <div class="badges">
      <span class="badge" role="img" aria-label="Realtor membership badge"></span>
      <span class="badge badge-round" role="img" aria-label="Equal housing opportunity badge"></span>
    </div>
    <div class="divider"></div>
    <div class="contact">
      <p class="agent-name">Tobias Merrow, PA</p>
      <p class="agent-title">Realtor</p>
      <p class="address">482 Linden Crest<br>Dr. Maple Hollow, FL 32790</p>
      <ul class="contact-list">
        <li>
          <svg viewBox="0 0 10 10" aria-hidden="true"><path fill="var(--red)" d="M2.2 0.8 3.6 0.6 4.3 2.8 3.3 3.6C3.8 4.8 5 6.1 6.3 6.7L7.1 5.7 9.3 6.4 9.1 7.8C8.9 8.8 7.8 9.4 6.8 9 3.9 8 1.9 6 0.9 3.1 0.6 2.1 1.2 1 2.2 0.8Z"/></svg>
          555.013.2478
        </li>
        <li>
          <svg viewBox="0 0 10 10" aria-hidden="true"><rect x="0.5" y="2" width="9" height="6" fill="var(--red)"/><path d="M0.8 2.3 5 5.5 9.2 2.3" fill="none" stroke="#fff" stroke-width="0.8"/></svg>
          hello@tobiasmerrowkl.com
        </li>
        <li>
          <svg viewBox="0 0 10 10" aria-hidden="true"><g fill="none" stroke="var(--red)" stroke-width="0.9"><circle cx="5" cy="5" r="4.2"/><ellipse cx="5" cy="5" rx="1.8" ry="4.2"/><path d="M0.8 5h8.4"/></g></svg>
          tobiasmerrowkl.com
        </li>
      </ul>
    </div>
    <svg class="footer-band" viewBox="0 0 499 25" aria-hidden="true">
      <rect x="0" y="0" width="170" height="25" fill="var(--red)"/>
      <polygon points="168,0 499,0 499,25 148,25" fill="var(--navy)"/>
    </svg>
  </section>

  <section class="card card-back" aria-label="Business card back">
    <div class="brand-name">
      <span class="brand-line-main">Brightgate</span>
      <span class="brand-line-sub">Realty Group</span>
    </div>
    <p class="back-website">tobiasmerrowkl.com</p>
  </section>
</main>
</body>
</html>
```